business card - Helicopter Flight Services, Flight School, etc.

We need a business card design for a new helicopter service.

We offer Helicopter Flight Services, Aerial Filming & Photography, Flight School, and Helicopter Tours. In that order.

Summit BladeAir, Inc.
Dennis Tollerby
SummitBladeair@Kestmail.com
626-418-7352

Based at the Brenwick Airport in Van Nuys, CA. The final design should communicate integrity and safety. Pictures or logos at your discretion.

Card back side - surprise me.

```html
<!DOCTYPE html>
<html lang="en">
<head>
<meta charset="utf-8">
<title>Summit BladeAir, Inc. — Business Card</title>
<link rel="stylesheet" href="https://fonts.googleapis.com/css2?family=Open+Sans:wght@400;600;700&display=swap">
<style>
  :root {
    --page-bg: #e9e7e3;
    --card-white: #ffffff;
    --brand-blue: #2a7fc9;
    --steel-light: #cfd1d4;
    --text-white: #ffffff;
    --text-soft: #d6ecfa;
  }
  * { margin: 0; padding: 0; box-sizing: border-box; }
  html, body {
    width: 1200px; height: 913px; overflow: hidden;
    background: var(--page-bg);
    font-family: "Open Sans", Arial, sans-serif;
  }
  .sheet {
    position: relative; width: 1200px; height: 913px;
    display: flex; align-items: center; justify-content: center; gap: 40px;
  }
  .card {
    position: relative; width: 520px; height: 298px;
    border-radius: 18px; overflow: hidden;
    background: var(--card-white);
    box-shadow: 0 6px 18px rgba(0,0,0,0.12);
  }
  /* Front */
  .card-front__bg { position: absolute; inset: 0; }
  .card-front__mark {
    position: absolute; left: 12px; top: 72px; width: 200px;
    display: flex; flex-direction: column; align-items: center; gap: 12px;
  }
  .mark-circle {
    width: 110px; height: 110px; border-radius: 50%;
    background: var(--steel-light); border: 4px solid var(--brand-blue);
  }
  .brand-name {
    font-weight: 600; color: var(--brand-blue); font-size: 17px; white-space: nowrap;
  }
  .contact {
    position: absolute; right: 22px; top: 46px; text-align: right;
    color: var(--text-white);
  }
  .contact__name { font-weight: 700; font-size: 20px; letter-spacing: 0.2px; line-height: 1.25; }
  .contact__role { font-size: 12px; color: var(--text-soft); }
  .contact__line {
    display: flex; justify-content: flex-end; align-items: center; gap: 6px;
    font-size: 12.5px; margin-top: 4px;
  }
  .contact__line--first { margin-top: 12px; }
  .contact__icon { width: 12px; height: 12px; flex: none; }
  /* Back */
  .card-back__lockup {
    position: absolute; left: 52px; top: 74px;
    display: flex; align-items: center; gap: 18px;
  }
  .card-back__lockup .mark-circle { width: 104px; height: 104px; }
  .divider { width: 1.5px; height: 70px; background: var(--brand-blue); }
  .card-back__lockup .brand-name { font-size: 26px; }
  .services {
    position: absolute; left: 0; right: 0; top: 200px;
    text-align: center; color: var(--brand-blue); font-size: 15px; line-height: 1.35;
  }
</style>
</head>
<body>
<main class="sheet">

  <section class="card card-front" aria-label="Card front">
    <svg class="card-front__bg" width="520" height="298" viewBox="0 0 520 298" aria-hidden="true">
      <defs>
        <linearGradient id="blueSweep" x1="0" y1="0" x2="0.3" y2="1">
          <stop offset="0" stop-color="#3eaee3"/>
          <stop offset="0.55" stop-color="#1f8fd6"/>
          <stop offset="1" stop-color="#0f6fbf"/>
        </linearGradient>
      </defs>
      <rect width="520" height="298" fill="url(#blueSweep)"/>
      <circle cx="90" cy="165" r="182" fill="#b5b8bc"/>
      <circle cx="90" cy="165" r="178" fill="#ffffff"/>
    </svg>
    <div class="card-front__mark">
      <div class="mark-circle"></div>
      <span class="brand-name">Summit BladeAir, Inc.</span>
    </div>
    <div class="contact">
      <p class="contact__name">Dennis Tollerby</p>
      <p class="contact__role">Owner</p>
      <p class="contact__line contact__line--first">626-418-7352
        <svg class="contact__icon" viewBox="0 0 24 24" aria-hidden="true"><path fill="#d6ecfa" d="M6.6 10.8a15.1 15.1 0 0 0 6.6 6.6l2.2-2.2c.3-.3.7-.4 1-.2 1.1.4 2.3.6 3.6.6.6 0 1 .4 1 1V20c0 .6-.4 1-1 1A17 17 0 0 1 3 4c0-.6.4-1 1-1h3.5c.6 0 1 .4 1 1 0 1.3.2 2.5.6 3.6.1.3 0 .7-.2 1z"/></svg>
      </p>
      <p class="contact__line">SummitBladeair@Kestmail.com
        <svg class="contact__icon" viewBox="0 0 24 24" aria-hidden="true"><rect x="3" y="5" width="18" height="14" rx="2" fill="none" stroke="#d6ecfa" stroke-width="2"/><path d="M3.5 6l8.5 7 8.5-7" fill="none" stroke="#d6ecfa" stroke-width="2"/></svg>
      </p>
    </div>
  </section>

  <section class="card card-back" aria-label="Card back">
    <div class="card-back__lockup">
      <div class="mark-circle"></div>
      <div class="divider"></div>
      <span class="brand-name">Summit BladeAir, Inc.</span>
    </div>
    <div class="services">
      <p>Aerial Filming &amp; Photography</p>
      <p>Flight School</p>
      <p>Helicopter Tours (In that order)</p>
    </div>
  </section>

</main>
</body>
</html>
```